KVR - Redesign (PSD Files Only)

Requirements for the site:

1. We need our logo recreated, please use the same design and change colors to work on a white background

2. The site is a "Wizard" based site, that takes the customer through the process of creating a unique web presence that suits there needs

3.Colors Needed - Main "Dark Blue" Secondary = "Dark Grey" -Other = "Light Grey and White"

4.We need a CRISP CLEAN DESIGN, simple design

5.Wireframes are a general layout and may be modified by you to enhance the design

6. We want a complete web 5.0 look with big buttons and text boxes

7.The more personality the better

8. Current Site brightpolehub.example

9.See attachments for wireframes

10. Designer should deliver PSD files, no coding is required

11. The portfolio wireframe, should look like the design of the artflockly portfolio template
Updates

KEEP IT SIMPLE.,.....

We like the quillmark scaffold style of designs

```html
<!DOCTYPE html>
<html lang="en">
<head>
<meta charset="utf-8">
<title>KVR – Request a Consultation</title>
<link href="https://fonts.googleapis.com/css2?family=Dosis:wght@400;500;600;700&family=Open+Sans:ital,wght@0,400;0,600;1,400&display=swap" rel="stylesheet">
<style>
:root{
  --navy:#002a52;
  --navy-deep:#05203f;
  --blue-band:#0a4473;
  --nav-active:#0c3f6e;
  --bar:#1c1c1c;
  --footer:#1f1f1f;
  --footer-strip:#191919;
  --page-grey:#d3d3d3;
  --line-grey:#e6e6e6;
  --field-border:#cfd6dd;
  --field-focus:#e8f1fd;
  --text-navy:#0a2a55;
  --orange-top:#ff9a2e;
  --orange-bot:#f47a00;
  --white:#ffffff;
}
*{box-sizing:border-box;margin:0;padding:0}
html,body{width:1200px;height:1032px;overflow:hidden}
body{position:relative;background:var(--page-grey);font-family:"Open Sans",sans-serif;color:var(--text-navy)}
.abs{position:absolute}

/* header */
.topbar{left:0;top:0;width:1200px;height:24px;background:#171717}
.band{left:0;top:24px;width:1200px;height:150px;background:radial-gradient(ellipse at 50% 60%,#0b5486 0%,var(--blue-band) 45%,#073560 100%)}
.navbar{left:117px;top:0;width:966px;height:46px;background:var(--bar);clip-path:polygon(0 50%,12px 100%,954px 100%,966px 50%,966px 0,0 0)}
.logo{left:151px;top:7px;width:34px;height:32px;border:2px solid var(--white);border-radius:50%;color:var(--white);font:700 11px "Dosis",sans-serif;display:flex;align-items:center;justify-content:center}
.nav{left:221px;top:0;height:46px;display:flex;font:500 21px "Dosis",sans-serif}
.nav a{color:var(--white);text-decoration:none;padding:0 10px;line-height:46px}
.nav a.active{background:var(--nav-active)}
.social-top{left:704px;top:10px;display:flex;gap:8px}
.social-top span{width:26px;height:26px;border-radius:50%;background:var(--white);display:block}
.phone-top{left:884px;top:4px;color:#e9e9e9;font:400 27px "Dosis",sans-serif;display:flex;align-items:center;gap:6px}
.step{left:0;width:1200px;top:70px;text-align:center;color:var(--white);font:500 16px "Dosis",sans-serif}
.title{left:0;width:1200px;top:86px;text-align:center;color:var(--white);font:700 36px "Dosis",sans-serif}
.title span.dots{font-size:22px;letter-spacing:1px;vertical-align:middle;margin:0 12px}
.notch{left:588px;top:162px;width:0;height:0;border-left:12px solid transparent;border-right:12px solid transparent;border-bottom:12px solid var(--white)}

/* panel */
.panel{left:129px;top:174px;width:942px;height:650px;background:var(--white);border-left:1px solid #c5c5c5;border-right:1px solid #c5c5c5}
.crumbs{left:171px;top:193px;font-size:13px;display:flex;gap:10px;align-items:center}
.crumbs .sep{font-weight:600;font-size:14px}
.crumbs .off{color:#8a8a8a}
.rule{top:226px;height:1px;background:var(--line-grey)}
.field{left:171px;width:420px;height:34px;border:1px solid var(--field-border);padding:0 12px;font-size:13px;line-height:32px;color:var(--text-navy)}
.field.focus{background:var(--field-focus);border-color:#b9cbe3}
.field.area{height:145px;line-height:20px;padding-top:7px}
.btn{background:linear-gradient(var(--orange-top),var(--orange-bot));color:var(--white);font:700 28px "Dosis",sans-serif;display:flex;align-items:center;justify-content:center;border:1px solid #e06e00}
.btn-main{left:351px;top:573px;width:243px;height:54px}
.btn-note{left:351px;top:630px;width:270px;font-size:16.5px;line-height:19px}
.vline{width:2px;background:var(--line-grey)}
.badge{width:136px;height:136px;border-radius:50%;background:var(--navy-deep);border:3px solid var(--navy);color:var(--white);font-size:18px;line-height:22px;text-align:center;display:flex;align-items:center;justify-content:center}
.info{left:154px;top:733px;width:891px;height:52px;background:var(--navy);display:flex;align-items:center;padding-left:17px;gap:11px;color:var(--white);font:italic 400 16px "Open Sans",sans-serif}
.info i{width:28px;height:28px;border-radius:50%;background:var(--white);color:var(--navy);font:italic 700 17px Georgia,serif;display:flex;align-items:center;justify-content:center}

/* footer */
.footer{left:0;top:824px;width:1200px;height:208px;background:var(--footer)}
.f-strip{left:129px;top:946px;width:948px;height:55px;background:var(--footer-strip)}
.f-links{left:129px;top:866px;color:var(--white);font-size:13px;line-height:19px}
.f-links .dot{margin:0 6px}
.f-social{left:498px;top:863px;display:flex;gap:8px}
.f-social span{width:38px;height:38px;border-radius:50%;background:var(--white);display:block}
.f-phone{left:498px;top:905px;color:#e9e9e9;font:400 27px "Dosis",sans-serif;display:flex;align-items:center;gap:4px}
.btn-foot{left:828px;top:862px;width:243px;height:55px}
.partner{left:129px;top:948px;width:156px;height:53px;background:var(--white);border-left:54px solid #3a6fd0}
</style>
</head>
<body>
<div class="abs topbar"></div>
<div class="abs band"></div>
<div class="abs navbar"></div>
<div class="abs logo">KVR</div>
<nav class="abs nav"><a href="#">Home</a><a href="#" class="active">About Us</a><a href="#">Portfolio</a><a href="#">Contact Us</a></nav>
<div class="abs social-top" aria-label="Social links"><span></span><span></span><span></span><span></span></div>
<div class="abs phone-top"><svg width="14" height="20" viewBox="0 0 14 20"><path d="M3 1l3 0 1 5-2 1c1 3 2 5 4 7l2-1 3 4-2 2c-6-1-11-9-10-15z" fill="#e9e9e9"/></svg>1800-555-0142</div>
<div class="abs step">FINAL STEP</div>
<div class="abs title"><span class="dots">••••••••</span>Request a Consultation<span class="dots">••••••••</span></div>
<div class="abs notch"></div>

<div class="abs panel"></div>
<div class="abs crumbs"><span>Level 1</span><span class="sep">»</span><span>Level 2</span><span class="sep">»</span><span>Level 3</span><span class="sep">»</span><span class="off">Level 4</span></div>
<div class="abs rule" style="left:129px;width:668px"></div>
<div class="abs rule" style="left:889px;width:182px"></div>
<svg class="abs" style="left:803px;top:183px" width="80" height="80" viewBox="0 0 80 80" aria-label="Progress gauge">
  <circle cx="40" cy="40" r="32" fill="none" stroke="#e3e3e3" stroke-width="13"/>
  <path d="M8 40A32 32 0 0 1 40 8" fill="none" stroke="#0a3b66" stroke-width="13"/>
  <path d="M40 18l2 22h-4z" fill="#111"/>
  <circle cx="40" cy="40" r="3.5" fill="#4a6a90"/>
</svg>

<div class="abs field focus" style="top:241px">Your Name</div>
<div class="abs field" style="top:283px">Email Address</div>
<div class="abs field" style="top:325px">Phone No.</div>
<div class="abs field" style="top:367px">Best Time to Call</div>
<div class="abs field area" style="top:409px">More information (if needed)</div>
<div class="abs btn btn-main">Request Consultant</div>
<div class="abs btn-note">Our web professionals will contact you to discuss your project</div>

<div class="abs vline" style="left:725px;top:440px;height:293px"></div>
<div class="abs vline" style="left:958px;top:440px;height:293px"></div>
<div class="abs vline" style="left:843px;top:555px;height:178px"></div>
<svg class="abs" style="left:650px;top:300px" width="390" height="290" viewBox="0 0 390 290">
  <g fill="none" stroke="#e3e3e3" stroke-width="5">
    <path d="M5 112A72 72 0 0 0 147 112"/>
    <path d="M238 112A72 72 0 0 0 380 112"/>
    <path d="M122 227A72 72 0 0 0 264 227"/>
  </g>
</svg>
<div class="abs badge" style="left:658px;top:311px">24x7<br>customer<br>support</div>
<div class="abs badge" style="left:891px;top:311px">100%<br>Momeyback<br>Guarantee</div>
<div class="abs badge" style="left:776px;top:426px">Save<br>100% on<br>Webdesign</div>

<div class="abs info"><i>i</i>As your full service marketing partner, we will deliver and end to end marketing solution for your business.</div>

<footer class="abs footer"></footer>
<div class="abs f-strip"></div>
<div class="abs f-links">Home<span class="dot">.</span>About Us<span class="dot">.</span>Portfolio<span class="dot">.</span>Contact Us<br>Copyright © 2014 KVR Studios - All Right Reserved<br>www.brightpolehub.example</div>
<div class="abs f-social" aria-label="Social links"><span></span><span></span><span></span><span></span></div>
<div class="abs f-phone"><svg width="14" height="20" viewBox="0 0 14 20"><path d="M3 1l3 0 1 5-2 1c1 3 2 5 4 7l2-1 3 4-2 2c-6-1-11-9-10-15z" fill="#e9e9e9"/></svg>1800-555-0142</div>
<div class="abs btn btn-foot">Request Consultant</div>
<div class="abs partner" role="img" aria-label="Partner certification badge"></div>
</body>
</html>
```